Velmarotix - world unique technology for better life - please let them know who am i at first sight

We need a new business card for company which is a provider of unique crystal based technology suitable for all living being. For more information and final design you can use our brochure (our colours are black and blue from brochure).
We use Verdana font

Industry/Entity Type

Business

Contact Information for Business Card

regular dimension

Font styles to use
Other font styles liked:
• Verdana

Requirements
Must have
• Logo
• name
• function/position
• phone
• mobile
• e-mail
• adress
Nice to have
• inovative design (technology directed)

```html
<!DOCTYPE html>
<html lang="en">
<head>
<meta charset="utf-8">
<title>Velmarotix Technologies – Business Card</title>
<link href="https://fonts.googleapis.com/css2?family=Open+Sans:wght@300;400;700&display=swap" rel="stylesheet">
<style>
  :root {
    --page-bg: #e6e6e4;
    --card-black: #060606;
    --brand-blue: #2aa7e0;
    --band-blue: #35a9df;
    --text-light: #f2f2f2;
    --text-muted: #c9c9c9;
    --card-white: #ffffff;
    --text-dark: #222222;
  }
  * { margin: 0; padding: 0; box-sizing: border-box; }
  html, body {
    width: 1200px; height: 948px; overflow: hidden;
    background: var(--page-bg);
    font-family: Verdana, "Open Sans", sans-serif;
  }
  .canvas { position: relative; width: 1200px; height: 948px; }

  /* Front card */
  .card-front {
    position: absolute; left: 70px; top: 304px;
    width: 600px; height: 343px;
    background: var(--card-black);
    box-shadow: 0 10px 30px rgba(0,0,0,.25);
    overflow: hidden;
  }
  .front-band {
    position: absolute; left: 0; top: 0; bottom: 0; width: 62px;
    background: var(--band-blue);
  }
  .brand-mark {
    position: absolute; left: 30px; top: 34px;
    width: 72px; height: 72px; border-radius: 50%;
    background: var(--card-black); border: 3px solid var(--brand-blue);
  }
  .brand-name {
    position: absolute; left: 120px; top: 30px;
    color: var(--brand-blue); font-weight: 300;
    font-size: 50px; letter-spacing: 1px; line-height: 1;
  }
  .brand-sub {
    position: absolute; left: 124px; top: 90px;
    color: var(--brand-blue); font-weight: 300;
    font-size: 15px; letter-spacing: 9px;
  }
  .contact-list {
    position: absolute; left: 92px; top: 160px;
    list-style: none; color: var(--text-light); font-size: 12px;
  }
  .contact-list li { display: flex; align-items: center; gap: 9px; height: 22px; }
  .contact-list svg { width: 12px; height: 12px; fill: var(--brand-blue); flex: none; }
  .contact-address { margin-top: 8px; }
  .person {
    position: absolute; right: 44px; bottom: 42px; text-align: right;
  }
  .person-name { color: var(--brand-blue); font-weight: 700; font-size: 20px; }
  .person-role { color: var(--text-muted); font-size: 14px; margin-top: 4px; }

  /* Back card */
  .card-back {
    position: absolute; left: 770px; top: 180px;
    width: 343px; height: 600px;
    background: var(--card-white);
    box-shadow: 0 10px 30px rgba(0,0,0,.2);
  }
  .back-mark {
    position: absolute; left: 92px; top: 200px;
    width: 160px; height: 160px; border-radius: 50%;
    background: var(--brand-blue);
  }
  .back-name {
    position: absolute; left: 0; right: 0; top: 385px; text-align: center;
    color: var(--brand-blue); font-size: 26px; font-weight: 300; letter-spacing: 1px;
  }
  .back-web {
    position: absolute; left: 34px; top: 300px;
    transform: translate(-50%, -50%) rotate(90deg);
    transform-origin: center;
    color: var(--text-dark); font-size: 13px; font-weight: 700;
    letter-spacing: 2px; white-space: nowrap;
  }
</style>
</head>
<body>
<div class="canvas">

  <section class="card-front">
    <div class="front-band"></div>
    <div class="brand-mark"></div>
    <div class="brand-name">VELMAROTIX</div>
    <div class="brand-sub">TECHNOLOGIES</div>

    <ul class="contact-list">
      <li>
        <svg viewBox="0 0 12 12"><path d="M2.5 0.5l2 2.3-1.1 1.4c.7 1.5 1.9 2.7 3.4 3.4l1.4-1.1 2.3 2-1.2 2.3C5 10.3 1.7 7 .2 1.7z"/></svg>
        014-382-5170
      </li>
      <li>
        <svg viewBox="0 0 12 12"><rect x="3" y="0" width="6" height="12" rx="1"/><rect x="4" y="1.5" width="4" height="7.5" fill="#060606"/></svg>
        014-382-5170
      </li>
      <li>
        <svg viewBox="0 0 12 12"><rect x="0" y="2" width="12" height="8" rx="1"/><path d="M0.5 2.5L6 7l5.5-4.5" stroke="#060606" stroke-width="1.2" fill="none"/></svg>
        info@velmarotix.com
      </li>
      <li>
        <svg viewBox="0 0 12 12"><circle cx="6" cy="6" r="5.5"/><path d="M0.5 6h11M6 .5c-2.5 3-2.5 8 0 11M6 .5c2.5 3 2.5 8 0 11" stroke="#060606" stroke-width="1" fill="none"/></svg>
        www.velmarotix.com
      </li>
      <li class="contact-address">Street Name, City Name, Zipcode-01234</li>
    </ul>

    <div class="person">
      <div class="person-name">Mira Kostelac</div>
      <div class="person-role">Founder and CEO</div>
    </div>
  </section>

  <section class="card-back">
    <div class="back-web">www.velmarotix.cu</div>
    <div class="back-mark"></div>
    <div class="back-name">VELMAROTIX</div>
  </section>

</div>
</body>
</html>
```